Northfield Builders Guild Business card

We are looking for a new business card design with photo included.
Our business is a nonprofit construction contractor membership organization. We offer business education, assist with business setup and licensing, provide safety training, and provide a member directory.
URL: www.builderslinkguild.org
Color code:
CMYK: 0 cyan, 42 magenta, 100 yellow, 0 black for Print.
Hexidecimal: #FF9900
RGB: R 255; G 153; B 0

```html
<!DOCTYPE html>
<html lang="en">
<head>
<meta charset="utf-8">
<title>Northfield Builders Guild – Business Card</title>
<link rel="stylesheet" href="https://fonts.googleapis.com/css2?family=Jost:wght@400;700;800&display=swap">
<style>
  :root {
    --brand-orange: #ff9900;
    --charcoal: #353334;
    --ink: #3a3a3a;
    --paper: #ffffff;
    --backdrop: #8a8a8a;
  }
  * { margin: 0; padding: 0; box-sizing: border-box; }
  html, body { width: 1200px; height: 1200px; overflow: hidden; }
  body { background: var(--backdrop); font-family: "Jost", sans-serif; position: relative; }

  .card { position: absolute; left: 262px; width: 686px; height: 392px; }
  .card--front { top: 165px; background: var(--paper); }
  .card--back { top: 653px; background: var(--charcoal); }

  .title-band {
    position: absolute; left: 0; top: 50px; width: 357px; height: 71px;
    background: var(--charcoal); padding: 14px 0 0 45px;
  }
  .title-band .person-name {
    color: var(--brand-orange); font-weight: 700; font-size: 26px;
    line-height: 1; letter-spacing: 0.2px; text-transform: uppercase;
  }
  .title-band .person-role { color: var(--paper); font-weight: 700; font-size: 18px; line-height: 1.2; }

  .brand-name {
    position: absolute; right: 46px; top: 52px; width: 276px;
    font-weight: 800; font-size: 35px; line-height: 0.98;
    color: var(--charcoal); text-transform: uppercase; text-align: left;
  }

  .contact-list {
    position: absolute; left: 53px; top: 278px; list-style: none;
    color: var(--ink); font-size: 16.5px; line-height: 19.7px;
  }
  .contact-list li { display: flex; align-items: center; gap: 7px; }
  .contact-list svg { width: 12px; height: 12px; flex: none; }

  .address {
    position: absolute; right: 46px; top: 295px; text-align: right;
    color: var(--ink); font-size: 16.5px; line-height: 19.7px; font-style: normal;
  }

  .brand-name--back {
    position: absolute; left: 0; right: 0; top: 130px; text-align: center;
    font-weight: 800; font-size: 56px; line-height: 1;
    color: var(--brand-orange); text-transform: uppercase;
  }
</style>
</head>
<body>
  <section class="card card--front">
    <div class="title-band">
      <p class="person-name">Daniel Reyes</p>
      <p class="person-role">President</p>
    </div>
    <p class="brand-name">Northfield Builders Guild</p>

    <ul class="contact-list">
      <li>
        <svg viewBox="0 0 12 12" aria-hidden="true"><path fill="#ff9900" d="M2.3 0.5 4 2.6 3.1 4c.6 1.6 2.3 3.3 3.9 3.9L8.4 7l2.1 1.7-.9 2.2C5.2 11 1 6.8 1.1 1.4z"/></svg>
        (555) 210-4387
      </li>
      <li>
        <svg viewBox="0 0 12 12" aria-hidden="true"><rect x="3" y="0.5" width="6" height="11" rx="1" fill="none" stroke="#ff9900" stroke-width="1.2"/><circle cx="6" cy="9.5" r="0.7" fill="#ff9900"/></svg>
        555.318.0642
      </li>
      <li>
        <svg viewBox="0 0 12 12" aria-hidden="true"><rect x="0.5" y="2.5" width="11" height="7" fill="#ff9900"/><path d="M0.8 3 6 6.8 11.2 3" fill="none" stroke="#fff" stroke-width="1"/></svg>
        hello@nfbguild.org
      </li>
      <li>
        <svg viewBox="0 0 12 12" aria-hidden="true"><circle cx="6" cy="6" r="5.5" fill="#ff9900"/><path d="M3 3.5c1 .2 1.6 1 1.3 2 1 .4 1.2 1.5.6 2.4M7.5 1.2c-.3 1 .3 1.8 1.3 1.8.7 1 .5 2.2 1.6 2.8" fill="none" stroke="#fff" stroke-width="0.9"/></svg>
        www.builderslinkguild.org
      </li>
    </ul>

    <address class="address">
      2400 Meadow Ridge Rd<br>
      Suite #210<br>
      Northfield, OR 97000
    </address>
  </section>

  <section class="card card--back">
    <p class="brand-name--back">Northfield<br>Builders Guild</p>
  </section>
</body>
</html>
```